Summit Ridge Business Card

Side 1: Summit Ridge Logo (logo without Maltese cross) with industrial rope rescue related theme. Our company services - TRAINING - Fire Training, Confined Space Rescue Training, Rope Rescue training, Hazmat Training, Incident Command, EMS, Pump Operations Training. Website - summitridgeexample.com.
Side 2: Summit Ridge Fire Department Logo (logo with Maltese cross) with Firefighter related theme. Company (division) services - FIELD SERVICES - Fire Department, Stand-by Rescue, Safety, EMS, Planning. "Supporting the Emergency Response Community Since 1967"

Add contact information wherever it makes since (Name, Email, Phone).
I would like it to represent the Summit Ridge Fire Department Logo as a division not as a separate entity without saying it, possibly by depicting it in the background of Side 2 instead of being a standalone picture like the logo on Side 1.

```html
<!DOCTYPE html>
<html lang="en">
<head>
<meta charset="utf-8">
<title>Summit Ridge Business Card</title>
<link rel="stylesheet" href="https://fonts.googleapis.com/css2?family=Open+Sans:wght@400;600;700&display=swap">
<style>
  :root {
    --stage: #1d1d1f;
    --card: #232326;
    --card-edge: #2b2b2f;
    --red: #ec2227;
    --white: #f2f2f2;
    --grey: #9a9a9e;
    --font: "Open Sans", Arial, sans-serif;
  }
  * { box-sizing: border-box; margin: 0; padding: 0; }
  html, body { width: 1200px; height: 780px; overflow: hidden; background: var(--stage); }
  body { position: relative; font-family: var(--font); color: var(--white); }

  .card {
    position: absolute;
    width: 600px; height: 343px;
    background: var(--card);
    border: 1px solid var(--card-edge);
    box-shadow: 0 18px 40px rgba(0,0,0,.55);
    overflow: hidden;
  }

  /* ---------- Side 1: Training ---------- */
  .card--training { left: 540px; top: 40px; }
  .training__brand {
    position: absolute; top: 58px; left: 0; right: 0;
    display: flex; align-items: center; justify-content: center; gap: 16px;
  }
  .training__rule { width: 60px; height: 3px; background: var(--red); }
  .training__wordmark {
    font-weight: 700; font-size: 34px; letter-spacing: 3px;
    text-transform: uppercase; color: var(--red);
  }
  .training__heading {
    position: absolute; top: 140px; left: 40px; right: 40px;
    display: flex; align-items: center; gap: 14px;
  }
  .training__heading .line { flex: 1; height: 1px; background: var(--grey); }
  .training__heading .label {
    font-weight: 600; font-size: 15px; letter-spacing: 1px; color: var(--red);
  }
  .training__services {
    position: absolute; top: 172px; left: 40px; right: 40px;
    text-align: center; font-size: 13.5px; line-height: 1.75;
  }
  .dot { color: var(--red); font-size: 16px; margin: 0 5px; }
  .training__bottom-line {
    position: absolute; top: 240px; left: 40px; right: 40px;
    height: 1px; background: var(--grey);
  }
  .training__web {
    position: absolute; top: 256px; left: 0; right: 0;
    text-align: center; font-size: 14px;
  }

  /* ---------- Side 2: Field services / contact ---------- */
  .card--field { left: 60px; top: 400px; }
  .field__name-bar {
    position: absolute; left: 26px; top: 24px; width: 5px; height: 46px; background: var(--red);
  }
  .field__name {
    position: absolute; left: 42px; top: 22px;
    font-weight: 600; font-size: 24px; color: var(--red);
  }
  .field__title { position: absolute; left: 42px; top: 54px; font-size: 13px; }
  .field__address {
    position: absolute; left: 42px; top: 106px; font-size: 13px; line-height: 1.45;
  }
  .field__contacts {
    position: absolute; left: 42px; top: 158px; list-style: none;
    font-size: 13px; line-height: 1.6;
  }
  .field__contacts li { display: flex; align-items: center; gap: 8px; }
  .field__contacts svg { width: 12px; height: 12px; fill: var(--red); flex: none; }

  .field__brand {
    position: absolute; right: 36px; top: 40px; text-align: right;
  }
  .field__wordmark {
    font-weight: 700; font-size: 28px; letter-spacing: 4px;
    text-transform: uppercase; color: var(--white);
  }
  .field__division {
    margin-top: 8px; font-weight: 600; font-size: 15px; letter-spacing: .5px;
    color: var(--red); text-transform: uppercase;
  }
  .field__division::before {
    content: ""; display: inline-block; vertical-align: middle;
    width: 40px; height: 2px; background: var(--red); margin-right: 10px;
  }
  .field__services {
    position: absolute; right: 36px; top: 132px; list-style: none;
    text-align: right; font-size: 14px; line-height: 1.55;
  }
  .field__services li::after {
    content: ""; display: inline-block; width: 8px; height: 8px; border-radius: 50%;
    background: var(--red); margin-left: 9px; vertical-align: middle;
  }
  .field__band {
    position: absolute; left: 0; right: 0; bottom: 0; height: 40px;
    background: var(--red); display: flex; align-items: center; padding-left: 42px;
    font-size: 14px; color: var(--white);
  }
</style>
</head>
<body>

<section class="card card--training" aria-label="Business card side one: training">
  <div class="training__brand">
    <span class="training__rule"></span>
    <span class="training__wordmark">Summit Ridge</span>
    <span class="training__rule"></span>
  </div>
  <div class="training__heading">
    <span class="line"></span><span class="label">TRAINING</span><span class="line"></span>
  </div>
  <p class="training__services">
    <span class="dot">●</span>Fire Training<span class="dot">●</span>Confined Space Rescue Training<span class="dot">●</span>Rope Rescue training<br>
    <span class="dot">●</span>Hazmat Training<span class="dot">●</span>Incident Command<span class="dot">●</span>EMS<span class="dot">●</span>Pump Operations Training
  </p>
  <div class="training__bottom-line"></div>
  <p class="training__web">www.summitridgeexample.com</p>
</section>

<section class="card card--field" aria-label="Business card side two: field services">
  <span class="field__name-bar"></span>
  <h1 class="field__name">Mara Lindqvist</h1>
  <p class="field__title">Director</p>
  <p class="field__address">418 Harbor Lane<br>Northfield, TX 77000</p>
  <ul class="field__contacts">
    <li><svg viewBox="0 0 24 24" aria-hidden="true"><path d="M6.6 10.8a15 15 0 0 0 6.6 6.6l2.2-2.2c.3-.3.7-.4 1-.2 1.1.4 2.3.6 3.6.6.6 0 1 .4 1 1V20c0 .6-.4 1-1 1A17 17 0 0 1 3 4c0-.6.4-1 1-1h3.5c.6 0 1 .4 1 1 0 1.3.2 2.5.6 3.6.1.3 0 .7-.2 1z"/></svg>(555) 014-2290</li>
    <li><svg viewBox="0 0 24 24" aria-hidden="true"><path d="M12 2a10 10 0 1 0 0 20 10 10 0 0 0 0-20zm6.9 6h-3a15 15 0 0 0-1.3-3.9A8 8 0 0 1 18.9 8zM12 4c.8 1.2 1.5 2.5 1.9 4h-3.8c.4-1.5 1.1-2.8 1.9-4zM4.3 14a8 8 0 0 1 0-4h3.4a16 16 0 0 0 0 4zm.8 2h3a15 15 0 0 0 1.3 3.9A8 8 0 0 1 5.1 16zm3-8h-3a8 8 0 0 1 4.3-3.9C8.8 5.3 8.4 6.6 8.1 8zM12 20c-.8-1.2-1.5-2.5-1.9-4h3.8c-.4 1.5-1.1 2.8-1.9 4zm2.3-6H9.7a14 14 0 0 1 0-4h4.6a14 14 0 0 1 0 4zm.3 5.9c.6-1.2 1-2.5 1.3-3.9h3a8 8 0 0 1-4.3 3.9zm1.7-5.9a16 16 0 0 0 0-4h3.4a8 8 0 0 1 0 4z"/></svg>info@summitridgeexample.com</li>
    <li><svg viewBox="0 0 24 24" aria-hidden="true"><path d="M3 5h18c.6 0 1 .4 1 1v12c0 .6-.4 1-1 1H3c-.6 0-1-.4-1-1V6c0-.6.4-1 1-1zm9 7.5L4.5 7.5v1.8L12 14.3l7.5-5V7.5z"/></svg>www.summitridgeexample.com</li>
  </ul>

  <div class="field__brand">
    <p class="field__wordmark">Summit Ridge</p>
    <p class="field__division">Field Services</p>
  </div>
  <ul class="field__services">
    <li>EMS</li>
    <li>Safety</li>
    <li>Planning</li>
    <li>Fire Department</li>
    <li>Stand-by Rescue</li>
  </ul>

  <p class="field__band">Supporting the Emergency Response Community Since 1967</p>
</section>

</body>
</html>
```